Website for Excavator and Earthworks Company

We require a modern, sleek and practical website for our newly created earthworks/excavator business in Perth, Western Australia called Bluegum Ridge Earthworks.

The website should have a modern, cutting edge feel but only needs to be relatively simplistic in it's layout and eventual functionality.

Some pages it should have would be Home, About, Projects and Contact Us.

```html
<!DOCTYPE html>
<html lang="en">
<head>
<meta charset="utf-8">
<title>Bluegum Ridge Earthworks</title>
<link rel="stylesheet" href="https://fonts.googleapis.com/css2?family=Montserrat:wght@400;500;600;700;800&family=Krona+One&display=swap">
<style>
:root{
  --lime:#c9d32c;
  --orange:#d99a1e;
  --dark:#262626;
  --darker:#1a1a1a;
  --navy:#1b2a4e;
  --ink:#111;
  --text:#333;
  --white:#fff;
}
*{box-sizing:border-box;margin:0;padding:0}
html,body{width:1200px;height:3827px;overflow:hidden}
body{position:relative;background:var(--white);font-family:'Montserrat',sans-serif;color:var(--text)}
.abs{position:absolute}
.display{font-family:'Krona One',sans-serif}
.brand{display:flex;align-items:center;gap:10px;font-family:'Montserrat',sans-serif;font-weight:800;color:var(--ink);line-height:1.05}
.brand .mark{width:22px;height:22px;background:var(--lime)}
.btn{display:flex;align-items:center;justify-content:center;font-weight:700;font-size:12px;text-transform:uppercase;color:var(--ink);text-decoration:none}
.btn-lime{background:var(--lime)}
.pill{border-radius:40px}
.label{font-size:15px;color:var(--lime);text-transform:uppercase;display:flex;align-items:center;gap:8px}
.label::before,.label::after{content:"";width:30px;height:2px;background:var(--lime)}

/* header & hero */
.hero{left:0;top:0;width:1200px;height:650px;background:linear-gradient(180deg,#f6f5f2 0%,#ece7de 38%,#cbb99a 62%,#a58a5e 85%,#7b6748 100%)}
.hero-machine{left:270px;top:270px;width:880px;height:380px;background:radial-gradient(ellipse at 60% 45%,#e0a52a 0%,#c88c1e 35%,rgba(120,95,60,.0) 70%)}
.nav{top:35px;left:545px;display:flex;gap:27px;font-size:14px;font-weight:500;color:var(--ink)}
.hero h1{top:118px;left:0;width:1200px;text-align:center;font-size:44px;font-weight:800;color:var(--ink);letter-spacing:-.5px}
.hero h1 span{font-weight:400}
.hero p{top:180px;left:0;width:1200px;text-align:center;font-size:13px;font-weight:500;color:var(--ink)}

/* about */
.about-img-main{left:143px;top:731px;width:273px;height:432px;border-radius:0 0 0 110px;background:linear-gradient(160deg,#c8ccd0,#a68a4a 45%,#d9c93a 70%,#7a6a52)}
.about-img-circle{left:441px;top:725px;width:152px;height:152px;border-radius:50%;background:linear-gradient(160deg,#4d86c2,#d98a2a 55%,#7a5a3a)}
.about-img-tall{left:441px;top:900px;width:153px;height:263px;border-radius:80px 80px 0 0;background:linear-gradient(180deg,#6aa3d8,#e07a22 50%,#8a7054)}
.about-text{left:658px;top:750px;width:412px}
.about-text .eyebrow{font-size:11px;font-weight:500;color:var(--ink);text-transform:uppercase}
.about-text h2{margin-top:12px;font-size:33px;font-weight:800;color:var(--navy);line-height:1.3}
.about-text .rule{margin:6px 0 16px;width:115px;height:2px;background:var(--lime)}
.about-text p{font-size:12.5px;line-height:1.72;color:var(--ink);margin-bottom:8px}
.about-text .btn{margin-top:22px;width:123px;height:46px}

/* services */
.services{left:0;top:1256px;width:1200px;height:600px}
.svc-intro{left:0;top:0;width:413px;height:600px;background:linear-gradient(160deg,#555 0%,#333 45%,#6e5a2a 75%,#262626 100%)}
.svc-intro .label{position:absolute;left:100px;top:160px;font-size:15px}
.svc-intro .label::after{display:none}
.svc-intro h2{position:absolute;left:99px;top:187px;font-size:31px;color:var(--white);line-height:1.25}
.svc-intro p{position:absolute;left:99px;top:272px;width:250px;font-size:15px;line-height:1.85;color:var(--white)}
.tile{width:263px;height:300px;padding:0 26px 0 35px;color:var(--white)}
.tile.orange{background:var(--orange)}
.tile.dark{background:var(--dark)}
.tile svg{position:absolute;left:35px;top:52px}
.tile h3{position:absolute;left:35px;top:128px;font-family:'Krona One',sans-serif;font-size:15px;font-weight:400;line-height:1.35}
.tile p{position:absolute;left:35px;top:176px;width:205px;font-size:12px;line-height:1.6}

/* projects */
.projects-label{top:1944px;left:0;width:1200px;justify-content:center}
.projects-title{top:1978px;left:0;width:1200px;text-align:center;font-size:31px;color:var(--ink)}
.card{color:var(--white);display:flex;flex-direction:column;justify-content:flex-end;padding:0 12px 14px}
.card h4{font-family:'Krona One',sans-serif;font-weight:400;font-size:14px;margin-bottom:6px}
.card p{font-size:12px;line-height:1.45}

/* quote */
.quote{left:0;top:2551px;width:1200px;height:664px;background:linear-gradient(180deg,#2a2a26 0%,#1d1d1b 60%,#2b2a24 100%)}
.quote-label{top:2641px;left:0;width:1200px;justify-content:center}
.quote-title{top:2672px;left:0;width:1200px;text-align:center;font-size:36px;color:var(--white)}
.quote-sub{top:2716px;left:0;width:1200px;text-align:center;font-size:14px;line-height:1.55;color:var(--white)}
.form{left:211px;top:2786px;width:490px;height:316px;background:var(--white)}
.field{font-size:12px;color:var(--ink)}
.info{left:701px;top:2786px;width:288px;height:316px;background:var(--lime);color:var(--ink)}
.info h3{position:absolute;left:47px;top:34px;font-family:'Krona One',sans-serif;font-weight:400;font-size:15px;line-height:1.45}
.info-row{position:absolute;left:47px;display:flex;gap:14px;font-size:12px;line-height:1.5}
.social{display:flex;gap:8px}
.social span{width:26px;height:26px;border:1.5px solid var(--ink)}

/* newsletter */
.news-title{top:3305px;left:0;width:1200px;text-align:center;font-size:18px;color:var(--navy)}
.news-text{top:3343px;left:0;width:1200px;text-align:center;font-size:14px;line-height:1.55;color:var(--ink)}
.news-input{left:356px;top:3401px;width:333px;height:38px;border:1px solid #bbb;font-size:12px;padding:11px 12px;color:var(--ink)}
.news-btn{left:689px;top:3401px;width:153px;height:38px;background:var(--lime);font-family:'Krona One',sans-serif;font-size:14px;color:var(--navy);display:flex;align-items:center;justify-content:center}

/* footer */
.foot-rule{left:141px;top:3490px;width:918px;height:1px;background:#ddd}
.foot-nav{top:3636px;left:352px;display:flex;gap:40px;font-size:13px;color:var(--ink)}
.foot-nav .active{color:var(--lime)}
.foot-band{left:141px;top:3668px;width:918px;height:105px;background:var(--lime)}
.foot-item{position:absolute;top:34px;display:flex;gap:14px;font-size:13px;line-height:1.5;color:var(--ink)}
.copy{top:3785px;left:143px;font-size:12px;color:var(--ink)}
</style>
</head>
<body>

<!-- Hero -->
<section class="abs hero" aria-label="Hero">
  <div class="abs hero-machine" role="img" aria-label="Photo of a yellow excavator beside a rock pile with site workers in hi-vis"></div>
  <div class="abs brand" style="left:141px;top:32px;font-size:17px"><span class="mark"></span>BLUEGUM RIDGE<br>EARTHWORKS</div>
  <nav class="abs nav"><span>HOME</span><span>ABOUT</span><span>PROJECTS</span><span>CONTACT US</span></nav>
  <a class="abs btn btn-lime pill" style="left:900px;top:21px;width:171px;height:46px">Get a quote today</a>
  <h1 class="abs">EARTH MOVING EXCELLENCE <span>IN PERTH</span></h1>
  <p class="abs">Professional Excavation, Bulk Earthworks, Site Preparation And Land Development Services Across Perth And Western Australia.</p>
  <a class="abs btn btn-lime pill" style="left:422px;top:218px;width:169px;height:45px">Get a quote today</a>
  <a class="abs btn pill" style="left:606px;top:218px;width:172px;height:45px;border:1.5px solid #333">View our projects</a>
</section>

<!-- About -->
<section aria-label="About">
  <div class="abs about-img-main" role="img" aria-label="Photo of three site workers in hi-vis in front of an excavator"></div>
  <div class="abs about-img-circle" role="img" aria-label="Photo of workers on an earthworks site"></div>
  <div class="abs about-img-tall" role="img" aria-label="Photo of an orange excavator arm against a blue sky"></div>
  <div class="abs about-text">
    <div class="eyebrow">About us</div>
    <h2>BLUEGUM RIDGE<br>EARTH WORKS</h2>
    <div class="rule"></div>
    <p>Bluegum Ridge Earthworks is Perth's trusted partner for excavation and earthmoving solutions. Founded on principles of precision, reliability, and uncompromising quality, we've built our reputation one project at a time.</p>
    <p>Our team brings decades of combined experience to every job, from residential site preparation to large-scale commercial developments. We invest in the latest equipment and technology to ensure efficiency, safety, and superior results.</p>
    <a class="btn btn-lime">Work with us</a>
  </div>
</section>

<!-- Services -->
<section class="abs services" aria-label="Services">
  <div class="abs svc-intro" role="img" aria-label="Dark photo of an excavator under a stormy sky">
    <div class="label">What we do</div>
    <h2 class="display">OUR<br>SERVICES</h2>
    <p>Comprehensive earthmoving and excavation solutions for projects of all sizes across Perth and regional WA.</p>
  </div>

  <div class="abs tile orange" style="left:413px;top:0">
    <svg width="52" height="50" viewBox="0 0 52 50" fill="none" stroke="#fff" stroke-width="3"><rect x="4" y="22" width="26" height="14"/><rect x="8" y="38" width="22" height="8" rx="4"/><path d="M30 24 L42 6 L50 16"/><path d="M44 30 l6 -6"/></svg>
    <h3>Bulk<br>Earthworks</h3>
    <p>Large-scale cut and fill operations, land levelling, and soil compaction for subdivisions and commercial developments.</p>
  </div>
  <div class="abs tile dark" style="left:676px;top:0">
    <svg width="56" height="50" viewBox="0 0 56 50" fill="none" stroke="#fff" stroke-width="3"><path d="M4 46 H52"/><rect x="6" y="28" width="16" height="14"/><path d="M22 30 L36 14 L44 22"/><circle cx="46" cy="8" r="5"/></svg>
    <h3>Land<br>Clearing</h3>
    <p>Vegetation removal, stump grinding, and site preparation for residential, agricultural and commercial properties.</p>
  </div>
  <div class="abs tile orange" style="left:939px;top:0;width:261px">
    <svg width="54" height="50" viewBox="0 0 54 50" fill="none" stroke="#fff" stroke-width="3"><path d="M18 4 H30 L38 36 H10 Z"/><path d="M4 42 H50"/><path d="M14 20 H34"/></svg>
    <h3>Road &amp; Driveway<br>Construction</h3>
    <p>Formation, grading and compaction for access roads, farm tracks, and residential driveways.</p>
  </div>
  <div class="abs tile dark" style="left:413px;top:300px">
    <svg width="52" height="52" viewBox="0 0 52 52" fill="none" stroke="#fff" stroke-width="3"><path d="M4 4 H28 V48 H4 Z"/><path d="M28 14 Q44 20 48 48"/><path d="M10 30 H22 M10 38 H22"/></svg>
    <h3>Dam<br>&amp; Drainage</h3>
    <p>Dam construction, excavation, lining, and drainage solutions for flood mitigation and water management.</p>
  </div>
  <div class="abs tile orange" style="left:676px;top:300px">
    <svg width="52" height="52" viewBox="0 0 52 52" fill="none" stroke="#fff" stroke-width="3"><path d="M10 48 V6 H40"/><path d="M36 6 V18"/><rect x="30" y="18" width="12" height="10"/><path d="M4 48 H48"/><rect x="26" y="34" width="18" height="14"/></svg>
    <h3>Site<br>Preparation</h3>
    <p>Complete site preparation for residential and commercial construction, including slab foundations and pad preparation.</p>
  </div>
  <div class="abs tile dark" style="left:939px;top:300px;width:261px">
    <svg width="62" height="50" viewBox="0 0 62 50" fill="none" stroke="#fff" stroke-width="3"><path d="M4 18 H38 L34 36 H8 Z"/><circle cx="14" cy="42" r="4"/><circle cx="30" cy="42" r="4"/><circle cx="50" cy="18" r="9"/><circle cx="50" cy="18" r="3"/></svg>
    <h3>Material<br>Supply &amp; Removal</h3>
    <p>Supply of quality fill material, sand, gravel, and removal of excess spoil from your site.</p>
  </div>
</section>

<!-- Projects -->
<section aria-label="Projects">
  <div class="abs label projects-label">Creations</div>
  <h2 class="abs display projects-title">OUR PROJECTS</h2>
  <div class="abs card" style="left:141px;top:2051px;width:324px;height:154px;background:linear-gradient(180deg,#9aa4a8,#5e6a5a 55%,#2f3530)" role="img" aria-label="Photo of an excavator near a house in misty autumn hills">
    <h4>Lorem ipsum dolor sit amet,</h4><p>Duis autem vel eum iriure dolor in hendrerit in vulputate velit esse molestie consequat.</p>
  </div>
  <div class="abs card" style="left:141px;top:2217px;width:324px;height:241px;background:linear-gradient(160deg,#e2c27a,#a88442 45%,#3a2f22)" role="img" aria-label="Photo of an excavator at sunset">
    <h4>Lorem ipsum dolor sit amet,</h4><p>Duis autem vel eum iriure dolor in hendrerit in vulputate velit esse molestie consequat.</p>
  </div>
  <div class="abs card" style="left:477px;top:2051px;width:286px;height:227px;background:linear-gradient(170deg,#c59f6a,#9a7440 55%,#3f3224)" role="img" aria-label="Aerial photo of an excavator digging in sandy soil">
    <h4 style="margin-left:10px">Lorem ipsum dolorsit</h4><p style="margin-left:10px">Duis autem vel eum iriure dolor in hendrerit in vulputate velit esse mole.</p>
  </div>
  <div class="abs card" style="left:772px;top:2051px;width:287px;height:227px;background:linear-gradient(170deg,#7a8a5a,#8a7a3a 50%,#2e2c22)" role="img" aria-label="Photo of an excavator working among green vegetation">
    <h4 style="margin-left:8px">Lorem ipsum dolor amet</h4><p style="margin-left:8px">Duis autem vel eum iriure dolor in hendrerit in vulputate velit esse mole.</p>
  </div>
  <div class="abs card" style="left:477px;top:2288px;width:582px;height:170px;background:linear-gradient(90deg,#7e8a74,#5a6a4c 45%,#353a36)" role="img" aria-label="Aerial photo of roadworks through a suburban street">
    <div style="position:absolute;left:394px;top:36px;width:180px"><h4>Lorem ipsum<br>dolor sit amet,</h4><p>Duis autem vel eum iriure dolor in hendrerit in vulputate velit esse molestie consequat.</p></div>
  </div>
</section>

<!-- Quote -->
<section aria-label="Request a quote">
  <div class="abs quote" role="img" aria-label="Dark photo of machinery on a construction site"></div>
  <div class="abs label quote-label">Quick inquiry</div>
  <h2 class="abs display quote-title">REQUEST A QUOTE</h2>
  <p class="abs quote-sub">Ready to move earth? Contact our Perth team for a no-obligation<br>site assessment and quote.</p>
  <div class="abs form">
    <div class="abs field" style="left:25px;top:38px;width:204px">First name*<span class="abs" style="left:0;top:31px;width:204px;height:1px;background:#bbb"></span></div>
    <div class="abs field" style="left:256px;top:38px;width:204px">Last name*<span class="abs" style="left:0;top:31px;width:204px;height:1px;background:#bbb"></span></div>
    <div class="abs field" style="left:25px;top:94px;width:204px">Your phone*<span class="abs" style="left:0;top:31px;width:204px;height:1px;background:#bbb"></span></div>
    <div class="abs field" style="left:256px;top:94px;width:204px">Your email*<span class="abs" style="left:0;top:31px;width:204px;height:1px;background:#bbb"></span></div>
    <div class="abs field" style="left:25px;top:150px;width:435px">Message<span class="abs" style="left:0;top:70px;width:435px;height:1px;background:#bbb"></span></div>
    <a class="abs btn btn-lime" style="left:327px;top:251px;width:163px;height:37px;font-size:14px;font-weight:600">Submit now</a>
  </div>
  <div class="abs info">
    <h3>CONTACT<br>INFORMATION</h3>
    <div class="info-row" style="top:100px"><svg width="24" height="30" viewBox="0 0 24 30"><path d="M12 1C6 1 2 5.5 2 11c0 8 10 17 10 17s10-9 10-17C22 5.5 18 1 12 1z" fill="#111"/><circle cx="12" cy="11" r="4" fill="#c9d32c"/></svg><span>123, Building Name, Street<br>City, State XY 123456</span></div>
    <div class="info-row" style="top:150px"><svg width="24" height="24" viewBox="0 0 24 24" fill="none" stroke="#111" stroke-width="2.2"><path d="M5 3h4l2 5-3 2c1 3 3 5 6 6l2-3 5 2v4c0 1-1 2-2 2C10 21 3 14 3 5c0-1 1-2 2-2z"/></svg><span>PHONE<br>(123) 456 7890</span></div>
    <div class="info-row" style="top:201px"><svg width="24" height="20" viewBox="0 0 24 20"><rect x="1" y="2" width="22" height="16" fill="#111"/><path d="M1 2l11 9 11-9" fill="none" stroke="#c9d32c" stroke-width="2"/></svg><span>EMAIL<br>info@bluegumridge.com</span></div>
    <div class="abs social" style="left:50px;top:256px"><span></span><span></span><span></span><span></span></div>
  </div>
</section>

<!-- Newsletter -->
<section aria-label="Newsletter">
  <h2 class="abs display news-title">SUBSCRIBE TO OUR NEWSLETTER</h2>
  <p class="abs news-text">Want to keep up to date with all our latest news and information?<br>Enter your email below to be added to our mailing list.</p>
  <div class="abs news-input">Enter your email address</div>
  <div class="abs news-btn">SUBSCRIBE</div>
</section>

<!-- Footer -->
<footer>
  <div class="abs foot-rule"></div>
  <div class="abs brand" style="left:505px;top:3550px;font-size:19px"><span class="mark"></span>BLUEGUM RIDGE<br>EARTHWORKS</div>
  <div class="abs" style="left:855px;top:3505px;width:222px;height:182px;border-radius:40% 40% 10% 10%;background:radial-gradient(ellipse at 55% 55%,#e99a2a,#c97a18 45%,rgba(255,255,255,0) 72%)" role="img" aria-label="Illustration of an orange excavator"></div>
  <nav class="abs foot-nav"><span class="active">HOME</span><span>ABOUT US</span><span>SERVICES</span><span>PROJECTS</span><span>CONTACT US</span></nav>
  <div class="abs foot-band">
    <div class="foot-item" style="left:178px"><svg width="24" height="30" viewBox="0 0 24 30"><path d="M12 1C6 1 2 5.5 2 11c0 8 10 17 10 17s10-9 10-17C22 5.5 18 1 12 1z" fill="#111"/><circle cx="12" cy="11" r="4" fill="#c9d32c"/></svg><span>123, Building Name, Street<br>City, State XY 123456</span></div>
    <div class="foot-item" style="left:412px"><svg width="24" height="24" viewBox="0 0 24 24" fill="none" stroke="#111" stroke-width="2.2"><path d="M5 3h4l2 5-3 2c1 3 3 5 6 6l2-3 5 2v4c0 1-1 2-2 2C10 21 3 14 3 5c0-1 1-2 2-2z"/></svg><span>PHONE<br>(123) 456 7890</span></div>
    <div class="foot-item" style="left:578px"><svg width="26" height="20" viewBox="0 0 24 20"><rect x="1" y="2" width="22" height="16" fill="#111"/><path d="M1 2l11 9 11-9" fill="none" stroke="#c9d32c" stroke-width="2"/></svg><span>EMAIL<br>info@bluegumridge.com</span></div>
  </div>
  <p class="abs copy">© 2026 Bluegum Ridge Earthworks. All Rights Reserved.</p>
  <div class="abs social" style="left:925px;top:3777px"><span></span><span></span><span></span><span></span></div>
</footer>

</body>
</html>
```